The most modern business card ever !!!

Our company call “Vendalo”. Vendalo is a technology company specialized in cruises solutions. Out main product is a platform to reserve cruises. This is a revolutionary platform that make easier to travel agencies and final users to reserve cruises across dozen companies like tibba, wernu, hpv, dgb, etc..We are a “start up”, with a young team of developers and we want to transmit it.. For it, we want something different, a modern business card that represent cruises and technology.. When someone receive this card, this person should say: wowww this is different… this is modern… this is a cruise related company..
- diferent, modern
- traditions business card

```html
<!DOCTYPE html>
<html lang="en">
<head>
<meta charset="utf-8">
<title>Vendalo business card</title>
<link href="https://fonts.googleapis.com/css2?family=Work+Sans:wght@400;500;600&display=swap" rel="stylesheet">
<style>
:root{
  --bg:#c9c9c9;
  --ink:#161616;
  --paper:#ffffff;
  --accent:#1ea0e0;
  --rule:#222222;
  --muted:#333333;
}
*{box-sizing:border-box;margin:0;padding:0}
html,body{width:1200px;height:930px;overflow:hidden}
body{background:var(--bg);font-family:"Work Sans",sans-serif;position:relative}
.card{position:absolute;width:540px;height:310px;border-radius:22px;overflow:hidden;box-shadow:0 6px 18px rgba(0,0,0,.25)}
.card-front{left:90px;top:110px;background:var(--ink);display:flex;align-items:center;justify-content:center}
.wordmark{font-weight:500;letter-spacing:2px;display:flex;align-items:center;gap:12px}
.wordmark .dot{width:14px;height:14px;background:var(--accent)}
.card-front .wordmark{color:var(--paper);font-size:64px}
.card-back{left:570px;top:500px;background:var(--paper)}
.card-back .wordmark{position:absolute;right:34px;top:26px;color:var(--ink);font-size:46px}
.rule{position:absolute;height:1px;background:var(--rule)}
.rule-top{left:180px;right:34px;top:108px}
.rule-mid{left:34px;width:260px;top:196px}
.person{position:absolute;left:34px;top:134px}
.person-name{color:var(--accent);font-size:22px;font-weight:500;letter-spacing:.5px;text-transform:uppercase}
.person-role{color:var(--muted);font-size:14px;margin-top:2px}
.contacts{position:absolute;left:34px;top:208px;list-style:none;font-size:15px;color:var(--ink);letter-spacing:.5px}
.contacts li{display:flex;align-items:center;gap:8px;height:20px}
.contacts svg{width:10px;height:10px;fill:var(--accent)}
.contacts .hl{color:var(--accent)}
.address{position:absolute;right:34px;top:128px;text-align:right;font-size:14px;color:var(--ink);line-height:1.4;letter-spacing:.4px}
.swoosh{position:absolute;left:0;bottom:0;width:540px;height:80px}
</style>
</head>
<body>
<section class="card card-front" aria-label="Card front">
  <div class="wordmark"><span class="dot"></span>Vendalo</div>
</section>

<section class="card card-back" aria-label="Card back">
  <div class="wordmark"><span class="dot"></span>Vendalo</div>
  <div class="rule rule-top"></div>
  <div class="person">
    <div class="person-name">Daniel Reyes</div>
    <div class="person-role">Director</div>
  </div>
  <div class="rule rule-mid"></div>
  <ul class="contacts">
    <li><svg viewBox="0 0 10 10"><path d="M2 0h2l1 3-1.5 1a6 6 0 0 0 2.5 2.5L7 5l3 1v2c0 1-1 2-2 2A8 8 0 0 1 0 2c0-1 1-2 2-2z"/></svg>(555) 014-2290</li>
    <li><svg viewBox="0 0 10 10"><path d="M0 2h10v6H0z M1 3v.3l4 2.5 4-2.5V3L5 5.5z" fill-rule="evenodd"/></svg>info@vendalo.com.br</li>
    <li><svg viewBox="0 0 10 10"><circle cx="5" cy="5" r="5"/></svg>www.<span class="hl">vendalo</span>.com.br</li>
  </ul>
  <div class="address">27b Harbour Lane,<br>Westport, NZ, 7825</div>
  <svg class="swoosh" viewBox="0 0 540 80" preserveAspectRatio="none" aria-hidden="true">
    <path d="M0 80 L0 62 L330 62 C365 62 368 22 405 22 L540 22 L540 80 Z" fill="var(--ink)"/>
    <path d="M0 56 L322 56 C356 56 360 16 398 16 L540 16" fill="none" stroke="var(--ink)" stroke-width="2"/>
  </svg>
</section>
</body>
</html>
```